Pastor's Lantern: How To Help Church Leaders Remain Strong In Their Callings.

I have created a 250-page book tentatively entitled, Pastor's Lantern, subtitle: A Handbook To Help Church Leaders Remain Strong in Their Callings. The chapters are taken from my podcast of the same name on TuneVault and website: pastorslantern-example.com which will need updating soon. The purpose of the book is to provide practical solutions to pastors/leaders about everyday issues faced in ministry such as loneliness, financial challenges, a pastor's family problems, sexual temptation ...etc. You can get an idea of the topics from TuneVault.
Updates

As mentioned in the brief, I am looking for something that will communicate solutions. My podcast, Pastor's Lantern from which this material originates is all about practical help for local pastors in facing the challenges of daily ministry. The logo I sent was designed for concept purposes only. It does not need to be on the cover necessarily unless it feeds into the overall theme.

Target Market(s)

Pastors and Church Leaders in the Christian Faith

Industry/Entity Type

Religious

Font styles to use
Serif

Colors

Designer to choose colors to be used in the design.

Requirements
Must have
• Crisp copy and lines. People see covers for 3 seconds. If they are not drawn in by complicated themes, I have failed. Many of the designs so far do not address the topic of the book in a way that impacts. This is about a toolbox or book that provides solutions to their everyday challenges. If it doesn't somehow point to tools, it should instead point to getting solutions.
Nice to have
• I have included a copy of my current logo. If you can incorporate it, fine. If you have a better idea, I am open to that and would be interested in contributing more if the logo is superior. The logo is not essential to either front or back cover..
Should not have
• Simplistic religious themes from often used pics. I will peruse other book covers in my genre. If I find the same pic used, it disqualifies the design immediately no matter how much I like it. Target audience is ministers. Simplistic cross designs have gotten less votes so far in polling. I want to grab attention with a compelling picture that communicates solutions.

```html
<!DOCTYPE html>
<html lang="en">
<head>
<meta charset="utf-8">
<title>Pastor's Lantern — Book Cover</title>
<link rel="stylesheet" href="https://fonts.googleapis.com/css2?family=Cinzel:wght@400;500&family=Staatliches&display=swap">
<style>
  :root {
    --paper: #ffffff;
    --author-grey: #4a4a4a;
    --sky-top: #2e2c2a;
    --sky-cloud: #5e5044;
    --sky-warm: #9a5a34;
    --glow: #d9561c;
    --horizon: #ee6a1e;
    --sea-upper: #e0581a;
    --sea-mid: #b83414;
    --sea-deep: #2a0c06;
    --title-beige: #e9dcc4;
    --title-white: #f4f2ef;
    --subtitle: #f6eee4;
    --imprint: #f4f2ef;
  }
  * { margin: 0; padding: 0; box-sizing: border-box; }
  html, body { width: 736px; height: 1200px; overflow: hidden; background: var(--paper); }
  .cover { position: relative; width: 736px; height: 1200px; overflow: hidden; background: var(--paper); }
  .author-band {
    position: absolute; top: 0; left: 0; width: 736px; height: 115px;
    display: flex; align-items: center; justify-content: center;
    background: var(--paper);
  }
  .author-name {
    font-family: "Cinzel", serif; font-weight: 400; font-size: 40px;
    letter-spacing: 0.16em; color: var(--author-grey); padding-top: 6px;
  }
  .sunset-scene {
    position: absolute; top: 115px; left: 0; width: 736px; height: 1085px;
    background:
      radial-gradient(ellipse 120px 40px at 65px 710px, rgba(255,220,120,0.9), rgba(255,150,60,0) 100%),
      linear-gradient(to bottom,
        var(--sky-top) 0%,
        var(--sky-cloud) 18%,
        var(--sky-warm) 35%,
        var(--glow) 55%,
        var(--horizon) 65.5%,
        var(--sea-upper) 67%,
        var(--sea-mid) 82%,
        var(--sea-deep) 100%);
  }
  .title-block {
    position: absolute; left: 0; width: 736px; text-align: center;
  }
  .title-small {
    top: 335px;
    font-family: "Staatliches", sans-serif; font-size: 74px; line-height: 1;
    letter-spacing: 0.38em; padding-left: 0.38em; color: var(--title-beige);
  }
  .title-large {
    top: 440px;
    font-family: "Staatliches", sans-serif; font-size: 176px; line-height: 1;
    letter-spacing: 0.01em; color: var(--title-white);
    text-shadow: 0 2px 6px rgba(0,0,0,0.25);
  }
  .subtitle {
    top: 640px;
    font-family: "Cinzel", serif; font-weight: 500; font-size: 25px; line-height: 32px;
    color: var(--subtitle); letter-spacing: 0.01em;
  }
  .imprint {
    position: absolute; top: 1080px; left: 0; width: 736px; text-align: center;
    font-family: "Cinzel", serif; font-weight: 500; font-size: 24px;
    color: var(--imprint); letter-spacing: 0.04em;
  }
</style>
</head>
<body>
  <main class="cover">
    <header class="author-band">
      <p class="author-name">CORWIN M. SALVATO</p>
    </header>
    <div class="sunset-scene" role="img" aria-label="Photograph of a calm sea at sunset with a small sailboat on the water and a distant low island"></div>
    <h1>
      <span class="title-block title-small">PASTOR'S</span>
      <span class="title-block title-large">LANTERN</span>
    </h1>
    <p class="title-block subtitle">A HANDBOOK TO HELP CHURCH LEADERS<br>REMAIN STRONG IN THEIR CALLINGS</p>
    <p class="imprint">Pastor's Lantern</p>
  </main>
</body>
</html>
```